Construction proffessionals servicing the inner suburbs of Melbournes NorthWest specialising in aler

I would like a web site that is sharp, contemporary and simple to navigate, ie.not too many pages. i would like a home page with some info about us, who we are what our history is and my passion for building and construction based on impeccable customer focus. i would like a projects page and somewhere for clients to add testimonials. i would like a project calculator as well so prospective clients can work out a rough budget prior to contacting. i would like the colours to be in line with my logo which i have uploaded. i have many photos which can be used and can be shared via drop box when required. I would like it to be personal to capture our transparent process. i would like to add our company process as well. be brave and take risks.

Target Market(s)

People renovating and extending their homes, people needing inspections on new homes and pre-purchase inspections

Industry/Entity Type

Construction

Number of Pages Required

5+ page

Requirements
Must have
• Professional, easy to navigate, provide viewers with a happy experience, look great, contacts, project calculator, link through to my training company www.qdmn.learnhub.example also check rowenhq on instagram for pics
Nice to have
• Links to instagram, fonts to match email signature

```html
<!DOCTYPE html>
<html lang="en">
<head>
<meta charset="utf-8">
<title>Rowen Group – Building &amp; Construction</title>
<link href="https://fonts.googleapis.com/css2?family=Open+Sans:wght@400;600;700&display=swap" rel="stylesheet">
<style>
:root{
  --orange:#f7941d;
  --orange-dark:#e07f0a;
  --ink:#333333;
  --muted:#777777;
  --light:#f2f2f2;
  --line:#dddddd;
  --footer:#3b3b3b;
  --footer-deep:#2e2e2e;
  --white:#ffffff;
}
*{box-sizing:border-box;margin:0;padding:0}
html,body{width:1200px;height:2288px;overflow:hidden}
body{font-family:"Open Sans",Arial,sans-serif;color:var(--ink);background:var(--white);position:relative}
a{color:inherit;text-decoration:none}

/* header */
.site-header{position:absolute;left:0;top:0;width:1200px;height:152px;background:var(--white)}
.brand{position:absolute;left:40px;top:36px;display:flex;align-items:center;gap:10px}
.brand-mark{width:34px;height:34px;background:var(--orange)}
.brand-name{font-size:30px;font-weight:700;color:var(--orange)}
.topbar-contact{position:absolute;left:170px;top:6px;font-size:12px;color:var(--muted);display:flex;gap:22px}
.socials{position:absolute;right:70px;top:8px;display:flex;gap:8px}
.socials span{width:18px;height:18px;border-radius:50%;background:#888}
.training-link{position:absolute;right:70px;top:62px;font-size:15px;font-weight:600;color:var(--ink)}
.training-link a{color:var(--orange)}
.main-nav{position:absolute;right:70px;top:100px;display:flex;gap:6px}
.main-nav a{font-size:14px;padding:8px 18px;color:var(--ink)}
.main-nav a.active{background:var(--orange);color:var(--white)}

/* hero */
.hero{position:absolute;left:0;top:152px;width:1200px;height:504px}
.hero-photo{position:absolute;inset:0;background:linear-gradient(135deg,#b9bec4 0%,#8f969d 40%,#d8a064 70%,#6b7077 100%)}
.hero-tagline{position:absolute;left:0;top:16px;width:1200px;height:36px;background:rgba(40,40,40,.7);color:var(--white);font-size:18px;font-weight:600;text-align:center;line-height:36px;letter-spacing:.3px}
.hero-bar{position:absolute;left:0;bottom:0;width:1200px;height:56px;background:var(--orange);display:flex;align-items:center;justify-content:space-between;padding:0 72px 0 82px}
.hero-bar p{color:var(--white);font-size:15px;font-weight:600}
.btn-light{background:var(--white);color:var(--ink);font-size:14px;font-weight:600;padding:9px 18px;border-radius:3px}

/* intro cards */
.intro{position:absolute;left:0;top:700px;width:1200px;height:400px}
.card{position:absolute;top:0;width:224px;text-align:center;background:var(--white);box-shadow:0 2px 8px rgba(0,0,0,.12);padding-bottom:18px}
.card-photo{height:200px}
.card h3{font-size:15px;font-weight:600;color:var(--orange-dark);margin:16px 0 8px}
.card p{font-size:11px;line-height:16px;color:var(--muted);padding:0 22px;margin-bottom:14px}
.btn-orange{display:inline-block;background:var(--orange);color:var(--white);font-size:12px;font-weight:600;padding:6px 16px;border-radius:3px}

/* methodology */
.methodology{position:absolute;left:0;top:1120px;width:1200px;height:300px;background:var(--light)}
.section-title{display:flex;align-items:center;justify-content:center;gap:18px;font-size:20px;font-weight:600;color:var(--ink)}
.section-title::before,.section-title::after{content:"";width:340px;height:1px;background:#bbb}
.methodology .section-title{position:absolute;left:0;top:36px;width:1200px}
.step{position:absolute;top:110px;width:250px;text-align:center}
.step-icon{width:50px;height:50px;margin:0 auto 14px}
.step h4{font-size:13px;font-weight:600;margin-bottom:10px}
.step p{font-size:11px;line-height:16px;color:var(--muted)}

/* projects */
.projects{position:absolute;left:0;top:1420px;width:1200px;height:530px}
.projects h2{position:absolute;left:0;top:22px;width:1200px;text-align:center;font-size:20px;font-weight:600}
.projects h2::after{content:"";display:block;width:60px;height:3px;background:var(--orange);margin:10px auto 0}
.project{position:absolute;top:100px;width:226px;text-align:center}
.project-photo{height:240px}
.project h3{font-size:14px;font-weight:600;color:var(--orange-dark);margin:18px 0 8px}
.project p{font-size:11px;line-height:16px;color:var(--muted);padding:0 18px;margin-bottom:14px}

/* footer */
.site-footer{position:absolute;left:0;top:1952px;width:1200px;height:336px;background:var(--footer);color:#cfcfcf}
.footer-cols{position:absolute;left:82px;top:30px;width:1040px;display:flex;gap:44px}
.footer-col{width:176px}
.footer-col h5{font-size:14px;font-weight:600;color:var(--orange);padding-bottom:8px;border-bottom:1px solid #555;margin-bottom:10px}
.footer-col li{list-style:none;font-size:11px;line-height:19px}
.blog li{display:flex;align-items:center;gap:6px}
.blog li::before{content:"";width:8px;height:8px;background:var(--white)}
.contact li{display:flex;align-items:center;gap:8px;margin-bottom:10px}
.foot-socials{display:flex;gap:6px;margin-top:8px}
.foot-socials span{width:22px;height:22px;border-radius:50%}
.footer-bottom{position:absolute;left:0;bottom:0;width:1200px;height:48px;background:var(--footer-deep);display:flex;align-items:center;justify-content:space-between;padding:0 82px;font-size:11px}
.footer-bottom a{color:var(--orange)}
</style>
</head>
<body>

<header class="site-header">
  <div class="topbar-contact"><span>+61 3 9000 0000</span><span>info@rowenhq.example</span></div>
  <div class="socials"><span></span><span></span><span></span><span></span></div>
  <a class="brand" href="#"><span class="brand-mark"></span><span class="brand-name">Rowen</span></a>
  <p class="training-link">Please Visit Our Training Company Website <a href="#">www.qdmn.learnhub.example</a></p>
  <nav class="main-nav">
    <a class="active" href="#">Home</a><a href="#">About Us</a><a href="#">Who We are</a><a href="#">Projects</a><a href="#">Testimonials</a><a href="#">Contact Us</a>
  </nav>
</header>

<section class="hero">
  <div class="hero-photo" role="img" aria-label="Two builders in hard hats and high-visibility vests reviewing plans on a construction site"></div>
  <p class="hero-tagline">PROVIDING QUALITY EXPERT ADVICE, COMMON SENSE AND FRIENDLY PROFESSIONAL SERVICE</p>
  <div class="hero-bar">
    <p>Lorem Ipsum is simply dummy text of the printing and typesetting industry.</p>
    <a class="btn-light" href="#">Project Calculator</a>
  </div>
</section>

<section class="intro">
  <article class="card" style="left:88px">
    <div class="card-photo" role="img" aria-label="Builders working on a timber frame" style="background:linear-gradient(160deg,#c9a27a,#8a6a4c)"></div>
    <h3>About Rowen Group</h3>
    <p>The standard chunk of Lorem Ipsum used since the 1500s is reproduced below for those interested. Sections 1.10.32 and</p>
    <a class="btn-orange" href="#">Read More</a>
  </article>
  <article class="card" style="left:488px">
    <div class="card-photo" role="img" aria-label="Team members meeting in an office" style="background:linear-gradient(160deg,#d7dbe0,#8d96a0)"></div>
    <h3>Who we are</h3>
    <p>The standard chunk of Lorem Ipsum used since the 1500s is reproduced below for those interested. Sections 1.10.32 and</p>
    <a class="btn-orange" href="#">Read More</a>
  </article>
  <article class="card" style="left:888px">
    <div class="card-photo" role="img" aria-label="Desk with plans, tablet and tools" style="background:linear-gradient(160deg,#e4e1d8,#a3a9b0)"></div>
    <h3>Our Services</h3>
    <p>The standard chunk of Lorem Ipsum used since the 1500s is reproduced below for those interested. Sections 1.10.32 and</p>
    <a class="btn-orange" href="#">Read More</a>
  </article>
</section>

<section class="methodology">
  <h2 class="section-title">Project Methodology</h2>
  <div class="step" style="left:150px">
    <svg class="step-icon" viewBox="0 0 50 50"><circle cx="25" cy="25" r="24" fill="#f7941d"/><rect x="15" y="18" width="20" height="16" fill="#fff"/></svg>
    <h4>Scheduling Labour and Material</h4>
    <p>Lorem Ipsum is simply dummy text of the printing and typesetting industry. Lorem Ipsum has been the industry's standard dummy text</p>
  </div>
  <div class="step" style="left:475px">
    <svg class="step-icon" viewBox="0 0 50 50"><circle cx="25" cy="25" r="24" fill="#f7941d"/><rect x="16" y="14" width="18" height="22" fill="#fff"/></svg>
    <h4>Estimating and Ordering Materials</h4>
    <p>Lorem Ipsum is simply dummy text of the printing and typesetting industry. Lorem Ipsum has been the industry's standard dummy text</p>
  </div>
  <div class="step" style="left:800px">
    <svg class="step-icon" viewBox="0 0 50 50"><circle cx="25" cy="25" r="24" fill="#f7941d"/><path d="M14 34 L25 16 L36 34 Z" fill="#fff"/></svg>
    <h4>Demolition</h4>
    <p>Lorem Ipsum is simply dummy text of the printing and typesetting industry. Lorem Ipsum has been the industry's standard dummy text</p>
  </div>
</section>

<section class="projects">
  <h2>Our Projects</h2>
  <article class="project" style="left:88px">
    <div class="project-photo" role="img" aria-label="Interior of a house under renovation with exposed framing" style="background:linear-gradient(160deg,#7a4a30,#c58a5a)"></div>
    <h3>Lorem Ipsum Dollar</h3>
    <p>The standard chunk of Lorem Ipsum used since the 1500s is reproduced below for those interested. Sections 1.10.32 and</p>
    <a class="btn-orange" href="#">Read More</a>
  </article>
  <article class="project" style="left:487px">
    <div class="project-photo" role="img" aria-label="Exterior of a completed brick home" style="background:linear-gradient(180deg,#a8c4de 0%,#a8c4de 35%,#b0503a 36%,#8a3c2c 100%)"></div>
    <h3>Lorem Ipsum Dollar</h3>
    <p>The standard chunk of Lorem Ipsum used since the 1500s is reproduced below for those interested. Sections 1.10.32 and</p>
    <a class="btn-orange" href="#">Read More</a>
  </article>
  <article class="project" style="left:886px">
    <div class="project-photo" role="img" aria-label="Hallway of a new extension during fit-out" style="background:linear-gradient(160deg,#e6e2da,#a99f90)"></div>
    <h3>Lorem Ipsum Dollar</h3>
    <p>The standard chunk of Lorem Ipsum used since the 1500s is reproduced below for those interested. Sections 1.10.32 and</p>
    <a class="btn-orange" href="#">Read More</a>
  </article>
</section>

<footer class="site-footer">
  <div class="footer-cols">
    <div class="footer-col blog">
      <h5>Visit Our Blog</h5>
      <ul><li>Contrary to popular belief, Lorem</li><li>Contrary to popular belief, Lorem</li><li>Contrary to popular belief, Lorem</li><li>Contrary to popular belief, Lorem</li><li>Contrary to popular belief, Lorem</li></ul>
    </div>
    <div class="footer-col">
      <h5>Quick Links</h5>
      <ul><li>Home</li><li>About Us</li><li>Who We are</li><li>Projects</li><li>Testimonials</li><li>Contact Us</li></ul>
    </div>
    <div class="footer-col">
      <h5>Services</h5>
      <ul><li>Lorem ipsum dollar</li><li>Contrary to popular</li><li>The standard chunk</li><li>Virginia looked up</li><li>Sections from the</li><li>Lorem ipsum dollar</li></ul>
    </div>
    <div class="footer-col">
      <h5>Important Links</h5>
      <ul><li>Lorem ipsum dollar</li><li>Lorem ipsum dollar</li><li>Lorem ipsum dollar</li><li>Lorem ipsum dollar</li><li>Lorem ipsum dollar</li><li>Lorem ipsum sit</li></ul>
    </div>
    <div class="footer-col contact">
      <h5>Contact Us</h5>
      <ul>
        <li><svg width="12" height="12" viewBox="0 0 12 12"><path d="M2 1 L4 1 L5 4 L3.5 5 Q5 8 7 8.5 L8 7 L11 8 L11 10 Q10 11 8 11 Q1 9 1 2 Z" fill="#cfcfcf"/></svg>+61 3 9000 0000</li>
        <li><svg width="12" height="10" viewBox="0 0 12 10"><rect x="0.5" y="0.5" width="11" height="9" fill="none" stroke="#cfcfcf"/><path d="M0.5 0.5 L6 5 L11.5 0.5" fill="none" stroke="#cfcfcf"/></svg>info@rowenhq.example</li>
      </ul>
      <div class="foot-socials"><span style="background:#3b5998"></span><span style="background:#1da1f2"></span><span style="background:#dd4b39"></span></div>
    </div>
  </div>
  <div class="footer-bottom"><span>© 2017 Company. All Rights Reserved.</span><a href="#">Privacy Statement</a></div>
</footer>

</body>
</html>
```